Business Card Design

We are a commercial real estate brokerage in San Francisco, leasing office buildings downtown.
I would like a clean, elegant look. Simple but powerful .

Industry/Entity Type

Business

Contact Information for Business Card

Derek Holloway
lic# 07258143
415.555.0172
derek@velt-commercial.example
velt-commercial.example

```html
<!DOCTYPE html>
<html lang="en">
<head>
<meta charset="utf-8">
<title>VELT Commercial – Business Card</title>
<link rel="stylesheet" href="https://fonts.googleapis.com/css2?family=Questrial&family=Open+Sans:ital,wght@0,400;0,600;1,400&display=swap">
<style>
  :root {
    --backdrop: #8d8d8d;
    --card: #e9eaec;
    --brand-blue: #5a6d8e;
    --ink: #4a4a4a;
    --ink-soft: #555a60;
    --skyline-light: rgba(190, 192, 196, 0.25);
    --skyline-dark: rgba(150, 152, 158, 0.75);
    --mark: #6a6d72;
  }
  * { box-sizing: border-box; margin: 0; padding: 0; }
  html, body {
    width: 1105px;
    height: 1200px;
    overflow: hidden;
    background: var(--backdrop);
  }
  .card {
    position: absolute;
    left: 180px;
    width: 746px;
    height: 426px;
    background: var(--card);
    overflow: hidden;
  }
  .card--front { top: 119px; }
  .card--back { top: 636px; }

  .skyline-art {
    position: absolute;
    left: 140px;
    top: 0;
    width: 606px;
    height: 426px;
    background: linear-gradient(90deg, var(--skyline-light) 0%, rgba(170,172,178,0.45) 55%, var(--skyline-dark) 100%);
  }

  .front-content {
    position: absolute;
    left: 63px;
    top: 52px;
  }
  .wordmark {
    font-family: "Questrial", sans-serif;
    color: var(--brand-blue);
    line-height: 1;
    text-transform: uppercase;
  }
  .wordmark__name { display: block; font-size: 78px; letter-spacing: 1px; }
  .wordmark__sub { display: block; font-size: 36px; letter-spacing: 1px; margin-top: 4px; }

  .agent-name {
    font-family: "Open Sans", sans-serif;
    font-weight: 600;
    font-size: 24px;
    color: var(--brand-blue);
    text-transform: uppercase;
    margin-top: 30px;
    letter-spacing: 0.5px;
  }
  .license {
    font-family: "Open Sans", sans-serif;
    font-size: 19px;
    color: var(--ink-soft);
    margin-top: 12px;
  }
  .contact-list {
    list-style: none;
    margin-top: 14px;
    font-family: "Open Sans", sans-serif;
    font-size: 19px;
    color: var(--ink-soft);
  }
  .contact-list li {
    display: flex;
    align-items: center;
    gap: 10px;
    height: 28px;
  }
  .contact-list svg { width: 17px; height: 17px; fill: var(--brand-blue); flex: none; }

  .back-logo {
    position: absolute;
    left: 0;
    right: 0;
    top: 150px;
    display: flex;
    justify-content: center;
    align-items: center;
    gap: 22px;
  }
  .back-logo__square {
    width: 60px;
    height: 60px;
    background: var(--mark);
  }
  .back-logo .wordmark__name { font-size: 62px; }
  .back-logo .wordmark__sub { font-size: 28px; }

  .tagline {
    position: absolute;
    left: 0;
    right: 0;
    top: 318px;
    text-align: center;
    font-family: "Open Sans", sans-serif;
    font-style: italic;
    font-size: 19px;
    line-height: 28px;
    color: var(--ink);
  }
</style>
</head>
<body>
  <section class="card card--front">
    <div class="skyline-art" role="img" aria-label="Faint illustration of downtown San Francisco office towers"></div>
    <div class="front-content">
      <h1 class="wordmark">
        <span class="wordmark__name">Velt</span>
        <span class="wordmark__sub">Commercial</span>
      </h1>
      <p class="agent-name">Derek Holloway</p>
      <p class="license">lic# 07258143</p>
      <ul class="contact-list">
        <li>
          <svg viewBox="0 0 24 24" aria-hidden="true"><path d="M6.6 10.8a15.1 15.1 0 0 0 6.6 6.6l2.2-2.2a1 1 0 0 1 1-.25 11.4 11.4 0 0 0 3.6.57 1 1 0 0 1 1 1V20a1 1 0 0 1-1 1A17 17 0 0 1 3 4a1 1 0 0 1 1-1h3.5a1 1 0 0 1 1 1c0 1.25.2 2.45.57 3.6a1 1 0 0 1-.25 1z"/></svg>
          415.555.0172
        </li>
        <li>
          <svg viewBox="0 0 24 24" aria-hidden="true"><path d="M2 5h20v14H2z M2 5l10 8 10-8" fill="none" stroke="var(--brand-blue)" stroke-width="0"/><path d="M2 5h20v2l-10 7L2 7z"/><path d="M2 9l10 7 10-7v10H2z"/></svg>
          derek@velt-commercial.example
        </li>
        <li>
          <svg viewBox="0 0 24 24" aria-hidden="true"><circle cx="12" cy="12" r="10"/><path d="M2 12h20M12 2c3 3 3 17 0 20M12 2c-3 3-3 17 0 20" stroke="#e9eaec" stroke-width="1.4" fill="none"/></svg>
          velt-commercial.example
        </li>
      </ul>
    </div>
  </section>

  <section class="card card--back">
    <div class="back-logo">
      <div class="back-logo__square" aria-hidden="true"></div>
      <p class="wordmark">
        <span class="wordmark__name">Velt</span>
        <span class="wordmark__sub">Commercial</span>
      </p>
    </div>
    <p class="tagline">commercial real estate brokerage in San Francisco<br>leasing office buildings downtown.</p>
  </section>
</body>
</html>
```